Additional Benefits of Working for VELMAR

Please prepare an infographic on the additional benefits besides salary of working at VELMAR as detailed in the attached word document. Also attached is our logo in eps and our company design "Grounds". We are a Not For Profit company that finds jobs for unemployed people of government benefit payments

Target Market(s)

Attracting people to work for VELMAR. Making VELMAR an employer of choice.

Font styles to use
Sans Serif

Colors

Designer to choose colors to be used in the design.

Requirements
Must have
• be on 1 page
• have our logo
Nice to have
• Our Grounds design worked into it.
• Happy engaged employees
• Community engagement - we are a not for profit organisation
Should not have
• Discrimination, swearing,

```html
<!DOCTYPE html>
<html lang="en">
<head>
<meta charset="utf-8">
<title>The Benefits of Working with Us – VELMAR</title>
<link href="https://fonts.googleapis.com/css2?family=Jost:wght@400;500;700;800&display=swap" rel="stylesheet">
<style>
  :root{
    --page:#ffffff;
    --panel-top:#eef6f3;
    --panel-bottom:#e3f0ec;
    --teal:#1d8a6e;
    --teal-dark:#0f6b55;
    --teal-light:#2aa585;
    --gold:#c98a2e;
    --gold-light:#e6b566;
    --gold-dark:#a86d1c;
    --ink:#1b2220;
    --ground-grey:#a7b0ae;
    --ground-teal:#8fd3bd;
    --ground-sand:#e4d3a8;
    --white:#ffffff;
  }
  *{box-sizing:border-box;margin:0;padding:0}
  html,body{width:1200px;height:990px;overflow:hidden;background:var(--page)}
  body{position:relative;font-family:"Jost",sans-serif;color:var(--ink)}

  .poster{position:absolute;left:222px;top:114px;width:756px;height:707px;
    background:linear-gradient(160deg,var(--panel-top),var(--panel-bottom))}

  .connectors{position:absolute;left:0;top:0;width:1200px;height:990px}
  .connectors path,.connectors line{stroke:var(--teal);stroke-width:3;fill:none}

  .title-banner{position:absolute;left:446px;top:140px;width:518px;height:61px;border-radius:20px;
    background:linear-gradient(180deg,var(--teal-light),var(--teal-dark));
    color:var(--white);font-size:37px;font-weight:400;letter-spacing:.3px;
    display:flex;align-items:center;justify-content:center;
    box-shadow:0 2px 3px rgba(0,0,0,.25)}

  .brand-badge{position:absolute;left:244px;top:140px;width:152px;height:152px;border-radius:50%;
    background:var(--white);display:flex;align-items:center;justify-content:center}
  .brand-name{font-size:38px;font-weight:800;color:var(--ink);letter-spacing:-1px}

  .icon-ring{position:absolute;width:100px;height:100px;border-radius:50%;
    background:linear-gradient(135deg,var(--teal-light),var(--teal-dark));
    display:flex;align-items:center;justify-content:center}
  .icon-ring .icon-face{width:82px;height:82px;border-radius:50%;background:var(--white);
    display:flex;align-items:center;justify-content:center}
  .icon-ring svg{width:52px;height:52px;fill:none;stroke:var(--teal);stroke-width:3;stroke-linecap:round;stroke-linejoin:round}

  .benefit-card{position:absolute;border:3px solid var(--gold);border-radius:14px;overflow:hidden;
    background:var(--ground-grey);display:flex;flex-direction:column}
  .card-head{position:relative;z-index:2;
    background:linear-gradient(180deg,var(--gold-light),var(--gold) 60%,var(--gold-dark));
    color:var(--white);text-align:center;font-size:15px;font-weight:400;line-height:18px;
    padding:4px 2px 5px;white-space:nowrap}
  .card-body{position:relative;flex:1}
  .grounds{position:absolute;inset:0;
    background:
      radial-gradient(ellipse 60% 40% at 20% 30%,var(--ground-teal),transparent 70%),
      radial-gradient(ellipse 50% 50% at 85% 75%,var(--ground-sand),transparent 70%),
      radial-gradient(ellipse 40% 60% at 60% 10%,var(--ground-teal),transparent 70%),
      linear-gradient(135deg,var(--ground-grey),#b7bfbc)}
  .card-list{position:relative;z-index:1;list-style:none;font-size:9px;line-height:14.5px;padding:5px 5px 3px 6px}
  .card-list li::before{content:"• "}
</style>
</head>
<body>
  <div class="poster"></div>

  <svg class="connectors" viewBox="0 0 1200 990" aria-hidden="true">
    <line x1="540" y1="266" x2="598" y2="266"/>
    <line x1="760" y1="263" x2="812" y2="263"/>
    <line x1="875" y1="330" x2="875" y2="362"/>
    <line x1="487" y1="325" x2="487" y2="362"/>
    <line x1="311" y1="500" x2="311" y2="528"/>
    <line x1="367" y1="549" x2="421" y2="549"/>
    <line x1="319" y1="622" x2="319" y2="655"/>
    <line x1="580" y1="518" x2="624" y2="518"/>
    <line x1="718" y1="511" x2="780" y2="511"/>
    <line x1="666" y1="441" x2="666" y2="472"/>
    <line x1="696" y1="566" x2="696" y2="602"/>
    <line x1="518" y1="572" x2="518" y2="599"/>
    <line x1="579" y1="660" x2="601" y2="660"/>
    <line x1="760" y1="640" x2="780" y2="640"/>
    <line x1="679" y1="708" x2="679" y2="720"/>
    <path d="M727 788 H862 Q875 788 875 775 V732"/>
  </svg>

  <div class="brand-badge"><span class="brand-name">VELMAR</span></div>

  <h1 class="title-banner">The Benefits of Working with Us</h1>

  <div class="icon-ring" style="left:442px;top:227px">
    <div class="icon-face">
      <svg viewBox="0 0 48 48" aria-label="Heart"><path d="M24 41 C10 31 5 24 5 16 a9 9 0 0 1 19 -3 a9 9 0 0 1 19 3 c0 8 -5 15 -19 25z"/><path d="M24 36 C13 28 10 23 10 17 a5 5 0 0 1 14 -2 a5 5 0 0 1 14 2 c0 6 -3 11 -14 19z"/></svg>
    </div>
  </div>
  <div class="icon-ring" style="left:809px;top:234px">
    <div class="icon-face">
      <svg viewBox="0 0 48 48" aria-label="Wallet"><rect x="7" y="8" width="32" height="34" rx="2"/><line x1="7" y1="15" x2="39" y2="15"/><rect x="28" y="24" width="13" height="9" rx="1"/><circle cx="33" cy="28.5" r="1.2"/></svg>
    </div>
  </div>
  <div class="icon-ring" style="left:270px;top:524px">
    <div class="icon-face">
      <svg viewBox="0 0 48 48" aria-label="Balance scales"><line x1="24" y1="6" x2="24" y2="40"/><circle cx="24" cy="9" r="3"/><line x1="10" y1="15" x2="38" y2="15"/><path d="M10 15 L4 28 H16 Z"/><path d="M38 15 L32 28 H44 Z"/><path d="M4 28 a6 4 0 0 0 12 0"/><path d="M32 28 a6 4 0 0 0 12 0"/><line x1="16" y1="42" x2="32" y2="42"/></svg>
    </div>
  </div>
  <div class="icon-ring" style="left:621px;top:470px">
    <div class="icon-face">
      <svg viewBox="0 0 48 48" aria-label="Rising chart"><line x1="5" y1="43" x2="43" y2="43"/><line x1="5" y1="5" x2="5" y2="43"/><line x1="12" y1="43" x2="12" y2="8"/><line x1="19" y1="43" x2="19" y2="12"/><line x1="26" y1="43" x2="26" y2="18"/><line x1="33" y1="43" x2="33" y2="24"/><path d="M8 36 L18 27 L25 31 L40 12"/><path d="M33 11 H41 V19"/></svg>
    </div>
  </div>
  <div class="icon-ring" style="left:629px;top:717px">
    <div class="icon-face">
      <svg viewBox="0 0 48 48" aria-label="Medal"><path d="M15 4 H33 V16 L24 20 L15 16 Z"/><circle cx="24" cy="31" r="12"/><path d="M24 24 l2.2 4.5 5 .7 -3.6 3.5 .9 5 -4.5 -2.4 -4.5 2.4 .9 -5 -3.6 -3.5 5 -.7z"/></svg>
    </div>
  </div>

  <section class="benefit-card" style="left:243px;top:263px;width:160px;height:238px">
    <h2 class="card-head">Life Balance</h2>
    <div class="card-body">
      <div class="grounds" role="img" aria-label="Company Grounds pattern in teal, grey and sand"></div>
      <ul class="card-list">
        <li>VELMAR Day Leave. An extra day off at Christmas</li>
        <li>BIRTHDAY Leave. A paid day off on your birthday</li>
        <li>A day off every month as Time In Lieu</li>
        <li>4 weeks Annual Leave</li>
        <li>Generous Personal Leave</li>
        <li>Support for parental leave for the birth or adoption of a child</li>
        <li>Flexible work arrangements</li>
      </ul>
    </div>
  </section>

  <section class="benefit-card" style="left:419px;top:360px;width:161px;height:212px">
    <h2 class="card-head">Wellbeing</h2>
    <div class="card-body">
      <div class="grounds" role="img" aria-label="Company Grounds pattern in teal, grey and sand"></div>
      <ul class="card-list">
        <li>Up to $450 per year to spend on Wellbeing services such as gym or yoga memberships</li>
        <li>Free counselling services 24x7 via our Employee Assistance Program</li>
        <li>Discount private health insurance</li>
        <li>WHS policies which support a safe, inclusive work place</li>
      </ul>
    </div>
  </section>

  <section class="benefit-card" style="left:598px;top:230px;width:162px;height:211px">
    <h2 class="card-head">Career Growth<br>&amp;Professional<br>Development</h2>
    <div class="card-body">
      <div class="grounds" role="img" aria-label="Company Grounds pattern in teal, grey and sand"></div>
      <ul class="card-list">
        <li>Ongoing internal training and development opportunities</li>
        <li>External study support @ study leave</li>
        <li>Access to the tools and technology to do your job well</li>
        <li>Career advancement opportunities</li>
        <li>Internal job vacancy listing</li>
      </ul>
    </div>
  </section>

  <section class="benefit-card" style="left:778px;top:360px;width:162px;height:188px">
    <h2 class="card-head">Remuneration<br>&amp; Salary Packaging</h2>
    <div class="card-body">
      <div class="grounds" role="img" aria-label="Company Grounds pattern in teal, grey and sand"></div>
      <ul class="card-list">
        <li>Competetive salary</li>
        <li>Ability to salary package up to $15,900 and reduce your tax. Package rent, home loans, child care and much more</li>
        <li>Salary package up to $2,650 on meal entertainment and holiday accommodation</li>
      </ul>
    </div>
  </section>

  <section class="benefit-card" style="left:241px;top:653px;width:160px;height:148px">
    <h2 class="card-head">Diversity &amp; Inclusion</h2>
    <div class="card-body">
      <div class="grounds" role="img" aria-label="Company Grounds pattern in teal, grey and sand"></div>
      <ul class="card-list">
        <li>An inclusive and diverse culture where different backgrounds, experiences and perspectives are valued</li>
        <li>Gender diversity. Over 50% of our workforce and our leaders are female</li>
      </ul>
    </div>
  </section>

  <section class="benefit-card" style="left:418px;top:597px;width:161px;height:198px">
    <h2 class="card-head">Benefits</h2>
    <div class="card-body">
      <div class="grounds" role="img" aria-label="Company Grounds pattern in teal, grey and sand"></div>
      <ul class="card-list">
        <li>Discounted vouchers for Grocera, Freshway, SoundBay, Reelhouse, Cellar Row, ValuMart, TrailCo and many others via Perkwise e-wallet</li>
        <li>A range of other employee discounts are also available, including access to discounted banking and finance, vehicle purchasing, leasing and hotel accomodation</li>
      </ul>
    </div>
  </section>

  <section class="benefit-card" style="left:599px;top:600px;width:161px;height:108px">
    <h2 class="card-head">Recognition</h2>
    <div class="card-body">
      <div class="grounds" role="img" aria-label="Company Grounds pattern in teal, grey and sand"></div>
      <ul class="card-list">
        <li>We celebrate our people reaching service milestones</li>
        <li>Team &amp; individual recognition for high performance</li>
      </ul>
    </div>
  </section>

  <section class="benefit-card" style="left:778px;top:572px;width:162px;height:164px">
    <h2 class="card-head">Contributing to<br>Community</h2>
    <div class="card-body">
      <div class="grounds" role="img" aria-label="Company Grounds pattern in teal, grey and sand"></div>
      <ul class="card-list">
        <li>Team involvement in local charity and community events</li>
        <li>Participation in VELMAR's 1000 Jobs in 100 days</li>
        <li>Strong relationships and connection with Indigenous Communities in support of Indigenous Employment</li>
      </ul>
    </div>
  </section>
</body>
</html>
```